Business Card for Fashion House

We need a business card design for our personalize fashion service for our customers. the business card should reflect reliability, luxury and creativity.
The brand Gravetto is extracted from "Graceful Velvetto"; Gravetto provides fashion designs sprinkled with luxury and style tailored for our elite clients character profile.
Gravetto is created for those who embody class and elegance with a passion for style.
Target Market(s)
Affluent Customers
Industry/Entity Type
Fashion
Contact Information for Business Card
Samira Haddadin
Fashion Designer
Telephone: +971 4 555 0192
Mobile +971 50 555 0147
Emal info@gravetto-example.com
Website www.gravetto-example.com
Social Media Youtube g+ Facebook Instagram Pin /gravetto
Font styles to use
Other font styles liked:
- Audrey provided
Look and feel
Each slider illustrates characteristics of the customer's brand and the style your logo design should communicate.

```html
<!DOCTYPE html>
<html lang="en">
<head>
<meta charset="utf-8">
<title>Gravetto Business Card</title>
<link rel="stylesheet" href="https://fonts.googleapis.com/css2?family=Marcellus&display=swap">
<style>
  :root {
    --backdrop: #d9dadc;
    --card: #000000;
    --ink: #ffffff;
    --accent-dark: #2a2a2a;
  }
  * { margin: 0; padding: 0; box-sizing: border-box; }
  html, body {
    width: 1200px; height: 1175px; overflow: hidden;
    background: var(--backdrop);
    font-family: "Marcellus", "Optima", serif;
    color: var(--ink);
  }
  .card {
    position: absolute;
    top: 438px;
    width: 532px; height: 304px;
    background: var(--card);
    overflow: hidden;
  }
  .card--front { left: 25px; }
  .card--back { left: 613px; }

  .brand-mark {
    position: absolute; left: 60px; top: 40px;
    display: flex; align-items: center; gap: 10px;
    font-size: 22px; letter-spacing: 0.08em;
  }
  .brand-mark__dot {
    width: 14px; height: 14px; border-radius: 50%;
    background: var(--ink);
  }
  .person { position: absolute; left: 43px; top: 138px; }
  .person__name { font-size: 17px; letter-spacing: 0.04em; text-transform: uppercase; }
  .person__role { font-size: 13px; letter-spacing: 0.03em; margin-top: 1px; }

  .contacts {
    position: absolute; left: 43px; top: 207px;
    list-style: none; font-size: 13.5px; letter-spacing: 0.05em;
  }
  .contacts li { display: flex; align-items: center; gap: 8px; height: 21px; }
  .contacts svg { width: 12px; height: 12px; flex: none; }

  .decoration { position: absolute; }
  .card--front .decoration { left: 330px; top: 70px; }
  .card--back .decoration { left: -120px; top: -110px; }

  .wordmark {
    position: absolute; right: 44px; top: 116px;
    font-size: 25px; letter-spacing: 0.42em; margin-right: -0.42em;
    text-transform: uppercase;
  }
  .handle {
    position: absolute; right: 46px; top: 158px;
    font-size: 15px; letter-spacing: 0.12em;
  }
  .website {
    position: absolute; right: 46px; top: 243px;
    font-size: 17px; letter-spacing: 0.14em;
  }
</style>
</head>
<body>
  <section class="card card--front" aria-label="Business card front">
    <div class="brand-mark"><span class="brand-mark__dot"></span>Gravetto</div>
    <div class="person">
      <p class="person__name">Samira Haddadin</p>
      <p class="person__role">Fashion Designer</p>
    </div>
    <ul class="contacts">
      <li>
        <svg viewBox="0 0 12 12"><circle cx="6" cy="6" r="6" fill="#fff"/><path d="M3.5 4.5h5l-.6 3.5H4.1z" fill="#000"/></svg>
        +971 50 555 0147
      </li>
      <li>
        <svg viewBox="0 0 12 12"><circle cx="6" cy="6" r="6" fill="#fff"/><rect x="4" y="2.8" width="4" height="6.4" rx="0.8" fill="#000"/></svg>
        +971 4 555 0192
      </li>
      <li>
        <svg viewBox="0 0 12 12"><circle cx="6" cy="6" r="6" fill="#fff"/><rect x="3" y="4" width="6" height="4" fill="#000"/></svg>
        info@gravetto-example.com
      </li>
    </ul>
    <svg class="decoration" width="260" height="260" viewBox="0 0 260 260" aria-hidden="true">
      <circle cx="130" cy="130" r="115" fill="none" stroke="var(--ink)" stroke-width="14"/>
    </svg>
  </section>

  <section class="card card--back" aria-label="Business card back">
    <svg class="decoration" width="320" height="320" viewBox="0 0 320 320" aria-hidden="true">
      <circle cx="160" cy="160" r="140" fill="none" stroke="var(--ink)" stroke-width="14"/>
    </svg>
    <p class="wordmark">Gravetto</p>
    <p class="handle">/gravetto</p>
    <p class="website">www.gravetto-example.com</p>
  </section>
</body>
</html>
```